business card Calvanto

Wee need a business card design for a new compagny based on Paris
We developped innovative a platform for selling services to refresh, beautify and develop its housing.
We would like a red logo on a black background
Te final design should communicate quality service, know-how, high-end

Target Market(s)

individuals

Industry/Entity Type

Business

```html
<!DOCTYPE html>
<html lang="en">
<head>
<meta charset="utf-8">
<title>Calvanto business card</title>
<link href="https://fonts.googleapis.com/css2?family=Open+Sans:wght@300;400;700&display=swap" rel="stylesheet">
<style>
  :root {
    --backdrop: #d9d9d9;
    --card: #ffffff;
    --brand-red: #e3605c;
    --ink: #2b2b2b;
    --wordmark-grey: #7a7a7a;
    --ghost: #f1f1f1;
    --band-black: #141414;
  }
  * { box-sizing: border-box; margin: 0; padding: 0; }
  html, body { width: 1200px; height: 852px; overflow: hidden; }
  body {
    background: var(--backdrop);
    font-family: "Open Sans", Arial, sans-serif;
    position: relative;
  }
  .card {
    position: absolute;
    width: 520px;
    height: 297px;
    background: var(--card);
    border-radius: 18px;
    overflow: hidden;
    box-shadow: 0 6px 18px rgba(0,0,0,0.18);
  }
  .card--front { left: 100px; top: 120px; }
  .card--back { left: 580px; top: 430px; }

  .ghost-square {
    position: absolute;
    right: 40px; top: -30px;
    width: 230px; height: 230px;
    background: var(--ghost);
    border-radius: 14px;
  }

  .brand {
    position: absolute;
    display: flex;
    align-items: center;
    gap: 14px;
  }
  .brand__square {
    width: 62px; height: 62px;
    background: var(--brand-red);
  }
  .brand__name {
    font-weight: 300;
    font-size: 50px;
    color: var(--wordmark-grey);
    letter-spacing: 0.5px;
    line-height: 1;
  }
  .card--front .brand { left: 150px; top: 118px; }
  .card--back .brand { left: 150px; top: 62px; }

  .contact {
    position: absolute;
    left: 290px; top: 150px;
    list-style: none;
    font-size: 11.5px;
    color: var(--ink);
    line-height: 18px;
  }
  .contact li { display: flex; align-items: center; gap: 7px; }
  .contact svg { width: 11px; height: 11px; fill: var(--brand-red); flex: none; }
  .contact .split { margin-left: 10px; display: inline-flex; align-items: center; gap: 7px; }

  .holder { position: absolute; left: 150px; top: 222px; text-align: center; }
  .holder__name { font-weight: 700; font-size: 16px; color: var(--brand-red); }
  .holder__role { font-size: 11.5px; color: var(--ink); }

  .band { position: absolute; inset: 0; width: 100%; height: 100%; }
</style>
</head>
<body>
  <section class="card card--front" aria-label="Card front">
    <div class="ghost-square"></div>
    <div class="brand">
      <div class="brand__square"></div>
      <span class="brand__name">Calvanto</span>
    </div>
  </section>

  <section class="card card--back" aria-label="Card back">
    <svg class="band" viewBox="0 0 520 297" preserveAspectRatio="none">
      <path d="M520 178 L420 232 Q395 246 365 250 L330 297 L520 297 Z" fill="var(--brand-red)"/>
      <path d="M520 188 L425 240 Q400 254 370 258 L340 297 L520 297 Z" fill="var(--band-black)"/>
    </svg>
    <div class="brand">
      <div class="brand__square"></div>
      <span class="brand__name">Calvanto</span>
    </div>
    <ul class="contact">
      <li><svg viewBox="0 0 12 12"><path d="M6 0a4 4 0 0 0-4 4c0 3 4 8 4 8s4-5 4-8a4 4 0 0 0-4-4zm0 5.5a1.5 1.5 0 1 1 0-3 1.5 1.5 0 0 1 0 3z"/></svg>Your long commercial of office address</li>
      <li><svg viewBox="0 0 12 12"><path d="M1 3c0-1 1-2 2-2h6c1 0 2 1 2 2v1H8V3H4v1H1zM2 5h8l1 6H1z"/></svg>000 0 0 000 00
        <span class="split"><svg viewBox="0 0 12 12"><path d="M3 0h5l1 1v3H3zM1 5h10v6H1zm2 2v1h2V7zm4 0v1h2V7z"/></svg>000 0 0 000 00</span></li>
      <li><svg viewBox="0 0 12 12"><path d="M0 2h12v1L6 7 0 3zm0 3l6 4 6-4v5H0z"/></svg>yourname@yourwebsite.com</li>
      <li><svg viewBox="0 0 12 12"><path d="M6 0a6 6 0 1 0 0 12A6 6 0 0 0 6 0zm0 1.2c.8.9 1.3 2.3 1.4 4.2H4.6c.1-1.9.6-3.3 1.4-4.2zM1.3 6.6h2.3c.1 1.5.4 2.8 1 3.8a4.8 4.8 0 0 1-3.3-3.8zm3.3 0h2.8c-.1 1.8-.6 3.2-1.4 4.2-.8-1-1.3-2.4-1.4-4.2zm3.8 0h2.3a4.8 4.8 0 0 1-3.3 3.8c.6-1 .9-2.3 1-3.8zM1.3 5.4a4.8 4.8 0 0 1 3.3-3.8c-.6 1-.9 2.3-1 3.8zm7.1 0c-.1-1.5-.4-2.8-1-3.8a4.8 4.8 0 0 1 3.3 3.8z"/></svg>www.yourwebsite.com</li>
    </ul>
    <div class="holder">
      <div class="holder__name">Your Long Name</div>
      <div class="holder__role">Managing Director</div>
    </div>
  </section>
</body>
</html>
```